Business card design needed

I need a business card design for a dog walking, dog minding and dog training business. Please refer to my website for the basic company colours and fonts I'm after. Planning on a double sided card, so all information doesn't need to be on the 'front' side.
Cheers

Industry/Entity Type

Dog Training

Contact Information for Business Card

Bramble Paws - gathering hounds
Rua 0498376214
bramblepaws.com.au
-walking
-holiday stays
-onsite care
-training and behavioural consultations

```html
<!DOCTYPE html>
<html lang="en">
<head>
<meta charset="utf-8">
<title>Bramble Paws – business card</title>
<link rel="stylesheet" href="https://fonts.googleapis.com/css2?family=Rokkitt:wght@500&family=Arimo&family=Marcellus+SC&family=Pinyon+Script&display=swap">
<style>
  :root {
    --backdrop: #e57718;
    --card-white: #ffffff;
    --brand-orange: #d2521c;
    --stripe-orange: #e8721c;
    --ink: #1e1e1e;
    --card-dark-top: #3a3a3a;
    --card-dark-bottom: #161616;
    --light-text: #f2f2f2;
    --photo-warm: #c9a27c;
    --photo-soft: #efe6dc;
  }
  * { margin: 0; padding: 0; box-sizing: border-box; }
  html, body { width: 1200px; height: 714px; overflow: hidden; }
  body { background: var(--backdrop); position: relative; }

  .card {
    position: absolute;
    top: 192px;
    width: 540px;
    height: 330px;
    border-radius: 22px;
    overflow: hidden;
    box-shadow: 0 6px 18px rgba(0,0,0,0.25);
  }

  /* Front */
  .card-front { left: 45px; background: var(--card-white); }
  .dog-photo {
    position: absolute;
    left: 40px; top: 28px;
    width: 470px; height: 104px;
    border-radius: 8px;
    background: linear-gradient(90deg, var(--photo-soft), var(--photo-warm) 55%, #a8643a);
  }
  .stripe {
    position: absolute;
    left: 0; top: 132px;
    width: 100%; height: 8px;
    background: var(--stripe-orange);
  }
  .brand-name {
    position: absolute;
    left: 0; right: 0; top: 168px;
    text-align: center;
    font-family: "Rokkitt", serif;
    font-weight: 500;
    font-size: 60px;
    letter-spacing: 1px;
    color: var(--brand-orange);
    text-transform: uppercase;
  }
  .tagline {
    position: absolute;
    left: 0; right: 0; top: 262px;
    text-align: center;
    font-family: "Arimo", sans-serif;
    font-size: 24px;
    color: var(--ink);
  }

  /* Back */
  .card-back {
    left: 615px;
    background: linear-gradient(160deg, var(--card-dark-top), var(--card-dark-bottom));
    border: 2px solid var(--card-white);
  }
  .services {
    position: absolute;
    left: 0; right: 0; top: 60px;
    list-style: none;
    text-align: center;
    font-family: "Marcellus SC", serif;
    font-size: 15px;
    line-height: 21px;
    letter-spacing: 2px;
    color: var(--light-text);
  }
  .contact {
    position: absolute;
    left: 70px; top: 228px;
    display: flex;
    align-items: center;
    gap: 22px;
  }
  .contact-name {
    font-family: "Pinyon Script", cursive;
    font-size: 40px;
    color: var(--stripe-orange);
  }
  .contact-lines {
    font-family: "Arimo", sans-serif;
    font-size: 16px;
    line-height: 26px;
    color: var(--light-text);
  }
  .contact-line { display: flex; align-items: center; gap: 6px; }
  .icon { width: 12px; height: 14px; flex: none; }
</style>
</head>
<body>
  <section class="card card-front">
    <div class="dog-photo" role="img" aria-label="Photo of five dogs of different breeds peeking over an orange rail"></div>
    <div class="stripe"></div>
    <h1 class="brand-name">Bramble Paws</h1>
    <p class="tagline">gathering hounds</p>
  </section>

  <section class="card card-back">
    <ul class="services">
      <li>Walking</li>
      <li>Holiday stays</li>
      <li>Onsite care</li>
      <li>Training</li>
      <li>&amp;</li>
      <li>Behavioural Consultations</li>
    </ul>
    <div class="contact">
      <span class="contact-name">Rua</span>
      <div class="contact-lines">
        <div class="contact-line">
          <svg class="icon" viewBox="0 0 12 14" aria-hidden="true">
            <rect x="2" y="0.5" width="8" height="13" rx="1.5" fill="#f2f2f2"/>
            <rect x="3.5" y="2" width="5" height="4" fill="#222"/>
          </svg>
          <span>: 049-837-6214</span>
        </div>
        <div class="contact-line">
          <svg class="icon" viewBox="0 0 12 14" aria-hidden="true">
            <rect x="0.5" y="1.5" width="11" height="11" fill="#f2f2f2"/>
            <path d="M2.5 5 L4 10 L6 6.5 L8 10 L9.5 5" stroke="#222" stroke-width="1.2" fill="none"/>
          </svg>
          <span>: www.bramblepaws.com.au</span>
        </div>
      </div>
    </div>
  </section>
</body>
</html>
```